Business card

We need a business card design for our company based in Auckland , New Zealand called 'Ridge + Studio Ltd'. We provide architectural services. We would like to see designs that use the max. three colours (such as white, black, grey) The final design should communicate financial safety and growth."
Also I will provide our company logo. I would like to the logo to be embeded onto our business card.

Target Market(s)

new residential house, alteration & addition & light commericila design & drafting service

Industry/Entity Type

Architecture

Contact Information for Business Card

Company name: ridge + studio Ltd.
Name: Mark Delford
Job title: architectural designer & Design LBP
email address: mark@rplusd.co.nz
mobile number: 02 5163 2290
web site: www.rplusd.co.nz

Requirements
Must have
• My project must have..
• - embeded logo (attached company logo)
• I don't have a bigger version for our company logo, but I have one old one, so you can remove the word from it)
• - insert the attached small BKTW logo & LBP logo
• - creative, simple and clear business card.
• - Max. three colours
Nice to have
• - Here are the samples I would like to share with you: http://www.plimvora.com/blog/minimalistic-business-card-designs/
• I would like to have my business card like one of the creation.
Should not have
• TBA

```html
<!DOCTYPE html>
<html lang="en">
<head>
<meta charset="utf-8">
<title>Ridge + Studio Ltd — Business Card</title>
<link href="https://fonts.googleapis.com/css2?family=Source+Sans+3:wght@400;600;700&display=swap" rel="stylesheet">
<style>
  :root {
    --backdrop: #e6e6e6;
    --card: #ffffff;
    --ink: #1e1e1e;
    --mark-grey: #6b6b6b;
    --badge-grey: #4a4a4a;
    --shadow: rgba(0, 0, 0, 0.28);
  }
  * { margin: 0; padding: 0; box-sizing: border-box; }
  html, body {
    width: 1200px;
    height: 830px;
    overflow: hidden;
    background: var(--backdrop);
    font-family: "Source Sans 3", sans-serif;
    color: var(--ink);
  }
  .canvas {
    position: relative;
    width: 1200px;
    height: 830px;
  }
  .card {
    position: absolute;
    top: 248px;
    width: 520px;
    height: 334px;
    background: var(--card);
    border-radius: 38px;
    box-shadow: 4px 6px 10px var(--shadow);
  }
  .card--front { left: 50px; }
  .card--back  { left: 630px; }

  .wordmark {
    display: flex;
    align-items: center;
    gap: 10px;
    color: var(--mark-grey);
    font-weight: 600;
    white-space: nowrap;
  }
  .wordmark__dot {
    border-radius: 50%;
    background: var(--mark-grey);
    flex: none;
  }
  .card--front .wordmark {
    position: absolute;
    left: 50%;
    top: 50%;
    transform: translate(-50%, -50%);
    font-size: 34px;
  }
  .card--front .wordmark__dot { width: 18px; height: 18px; }

  .back-content {
    position: absolute;
    left: 0;
    right: 0;
    top: 52px;
    display: flex;
    flex-direction: column;
    align-items: center;
    text-align: center;
  }
  .card--back .wordmark { font-size: 17px; gap: 7px; margin-bottom: 28px; }
  .card--back .wordmark__dot { width: 10px; height: 10px; }

  .company-name {
    font-size: 21px;
    font-weight: 700;
    line-height: 1.1;
  }
  .job-title {
    font-size: 11.5px;
    font-weight: 600;
    margin-top: 8px;
  }
  .person-name {
    font-size: 18px;
    font-weight: 400;
    margin-top: 12px;
  }
  .contact {
    list-style: none;
    margin-top: 10px;
    font-size: 15.5px;
    line-height: 20px;
  }
  .badge {
    position: absolute;
    right: 20px;
    bottom: 22px;
    width: 50px;
    height: 50px;
  }
</style>
</head>
<body>
<main class="canvas">
  <section class="card card--front" aria-label="Card front">
    <div class="wordmark">
      <span class="wordmark__dot"></span>
      <span class="wordmark__name">ridge + studio</span>
    </div>
  </section>

  <section class="card card--back" aria-label="Card back">
    <div class="back-content">
      <div class="wordmark">
        <span class="wordmark__dot"></span>
        <span class="wordmark__name">ridge + studio</span>
      </div>
      <h1 class="company-name">ridge + studio Ltd.</h1>
      <p class="job-title">architectural designer &amp; Design LBP</p>
      <p class="person-name">Mark Delford</p>
      <ul class="contact">
        <li>mark@rplusd.co.nz</li>
        <li>02 5163 2290</li>
        <li>www.rplusd.co.nz</li>
      </ul>
    </div>
    <svg class="badge" viewBox="0 0 50 50" role="img" aria-label="Licensed practitioner badge">
      <circle cx="25" cy="25" r="23" fill="none" stroke="var(--badge-grey)" stroke-width="2"/>
      <circle cx="25" cy="25" r="12" fill="var(--badge-grey)"/>
    </svg>
  </section>
</main>
</body>
</html>
```